Enterprise Application UI beautification

We have an enterprise application that is being redesigned. A screenshot from the new UX/UI is provided. The current UI design is OK but we would like it to look better. The key goals of the UI are to look like a premium product (think luxury brand) and for it to be visually very appealing/attractive. When people see the UI we want them to have a significant, positive reaction. They should "ooh" and "ahh". This is a product sold to large enterprises, not consumers. The current UI is a little plain. The colors we want to use are blue, yellow, black, white and gray. We probably don't want different colors but feel free to use any variations within or close to that color scheme that you see fit. Also feel free to modify the spacing, icons, widgets, tables, fonts, etc.

Target Market(s)

Large enterprise customers (Keystone 300).

Number of Pages Required

1 page

Font styles to use
Sans Serif

Colors
3277b5

Requirements
Must have
• A premium feel.

```html
<!DOCTYPE html>
<html lang="en">
<head>
<meta charset="utf-8">
<title>Data Sources</title>
<link href="https://fonts.googleapis.com/css2?family=Lato:wght@400;700&display=swap" rel="stylesheet">
<style>
:root{
  --navy-1:#0e1a2b;
  --navy-2:#1b3f66;
  --blue:#3277b5;
  --ink:#1c2230;
  --muted:#8a909c;
  --line:#e3e6ec;
  --canvas:#eef1f5;
  --rail:#111823;
  --rail-active:#1d2735;
  --gold:#e8b923;
  --gold-soft:#fbf1d0;
  --blue-soft:#e2ecf6;
  --icon:#9aa1ad;
  --icon-dark:#1c2230;
  --white:#ffffff;
}
*{box-sizing:border-box;margin:0;padding:0}
html,body{width:1200px;height:675px;overflow:hidden}
body{font-family:'Lato',sans-serif;background:var(--canvas);color:var(--ink);position:relative}
.abs{position:absolute}
.hero{left:339px;top:0;width:861px;height:337px;background:linear-gradient(115deg,var(--navy-1) 0%,var(--navy-2) 55%,var(--blue) 100%)}
.hero::after{content:"";position:absolute;left:0;right:0;bottom:0;height:2px;background:linear-gradient(90deg,transparent,var(--gold),transparent)}
.rail{left:0;top:0;width:74px;height:675px;background:var(--rail)}
.brand{left:12px;top:20px;display:flex;align-items:center;gap:5px;font-weight:700;font-size:13px;color:var(--white)}
.brand-dot{width:12px;height:12px;border-radius:50%;background:var(--gold)}
.rail-item{left:0;width:74px;height:62px;display:flex;align-items:center;justify-content:center}
.rail-item svg{width:20px;height:20px;fill:#6c7483}
.rail-item.active{background:var(--rail-active)}
.rail-item.active::after{content:"";position:absolute;right:0;top:0;width:4px;height:100%;background:var(--gold)}
.rail-item.active svg{fill:var(--gold);filter:drop-shadow(0 0 6px rgba(232,185,35,.55))}
.sources{left:74px;top:0;width:265px;height:675px;background:var(--white)}
.sources-title{left:24px;top:37px;font-size:16px;font-weight:400;color:var(--blue)}
.add-source{left:222px;top:37px;width:21px;height:21px;border-radius:50%;background:var(--gold-soft);display:flex;align-items:center;justify-content:center}
.search{left:24px;top:69px;width:219px;height:25px;border:1px solid #d8dce3;border-radius:3px;display:flex;align-items:center;gap:8px;padding-left:9px;font-size:9.5px;font-style:italic;color:#666c78}
.source{left:0;width:265px;height:61px;padding:17px 0 0 25px}
.source.selected{background:#f3f5f8;border-right:3px solid var(--gold)}
.source-name{font-size:11px;color:var(--ink)}
.source-type{font-size:9.5px;color:var(--muted);margin-top:2px}
.user{left:1020px;top:25px;display:flex;align-items:center}
.gear{width:26px;height:26px;border-radius:50%;background:rgba(255,255,255,.16);display:flex;align-items:center;justify-content:center}
.user-name{margin-left:24px;font-weight:700;font-size:11px;color:var(--white)}
.chev{left:1153px;top:34px}
.tool{top:77px;width:31px;height:31px;border-radius:50%;background:rgba(255,255,255,.16);display:flex;align-items:center;justify-content:center}
.meta{top:136px;height:45px;border:1px solid rgba(232,185,35,.55);border-radius:3px;background:rgba(255,255,255,.05);color:var(--white)}
.meta-field{position:absolute;top:11px}
.meta-label{font-size:7px;color:#c9d5e4}
.meta-value{font-size:10px;font-weight:700;margin-top:4px}
.add-fields{left:1059px;top:209px;width:75px;height:22px;border:1px solid var(--gold);border-radius:11px;background:var(--gold);color:var(--navy-1);font-size:9px;font-weight:700;display:flex;align-items:center;justify-content:center}
.card{left:339px;width:795px;background:var(--white)}
.card.open{top:248px;height:214px;box-shadow:0 4px 16px rgba(14,26,43,.12)}
.toggle{right:24px;top:12px;width:21px;height:21px;border-radius:50%;background:var(--blue-soft);display:flex;align-items:center;justify-content:center}
.rule{left:0;width:783px;height:1px;background:var(--line)}
.th{top:58px;font-size:10px;color:#5f6673}
.row-text{font-size:9.5px;color:var(--ink)}
.check{width:11px;height:11px;border:1px solid #8a909c;border-radius:1px;display:flex;align-items:center;justify-content:center}
.check.on{background:var(--blue);border-color:var(--blue)}
</style>
</head>
<body>
<svg width="0" height="0" style="position:absolute">
  <symbol id="i-search" viewBox="0 0 16 16"><circle cx="6.5" cy="6.5" r="4.5" fill="none" stroke="currentColor" stroke-width="1.6"/><path d="M10 10l4 4" stroke="currentColor" stroke-width="1.8"/></symbol>
  <symbol id="i-copy" viewBox="0 0 16 16"><rect x="2" y="2" width="9" height="9" fill="none" stroke="currentColor" stroke-width="1.3"/><rect x="5" y="5" width="9" height="9" fill="#fff" stroke="currentColor" stroke-width="1.3"/><path d="M7 8h5M7 10.5h5" stroke="currentColor"/></symbol>
  <symbol id="i-share" viewBox="0 0 16 16"><circle cx="12" cy="3.5" r="2.3"/><circle cx="4" cy="8" r="2.3"/><circle cx="12" cy="12.5" r="2.3"/><path d="M4 8l8-4.5M4 8l8 4.5" stroke="currentColor" stroke-width="1.5"/></symbol>
  <symbol id="i-target" viewBox="0 0 16 16"><circle cx="8" cy="8" r="4.5" fill="none" stroke="currentColor" stroke-width="1.5"/><circle cx="8" cy="8" r="1.6"/><path d="M8 1v3M8 12v3M1 8h3M12 8h3" stroke="currentColor" stroke-width="1.5"/></symbol>
  <symbol id="i-play" viewBox="0 0 16 16"><path d="M4 2l10 6-10 6z"/></symbol>
  <symbol id="i-clip" viewBox="0 0 16 16"><rect x="3" y="3" width="10" height="12" fill="none" stroke="currentColor" stroke-width="1.3"/><rect x="6" y="1.5" width="4" height="3"/><path d="M8 7v5M5.5 9.5h5" stroke="currentColor" stroke-width="1.2"/></symbol>
  <symbol id="i-card" viewBox="0 0 16 16"><rect x="1" y="3" width="14" height="10" rx="1" fill="none" stroke="currentColor" stroke-width="1.4"/><rect x="1" y="5.5" width="14" height="2"/></symbol>
  <symbol id="i-person" viewBox="0 0 16 16"><circle cx="8" cy="5" r="3.5"/><path d="M2 15c0-4 3-6 6-6s6 2 6 6z"/></symbol>
  <symbol id="i-pencil" viewBox="0 0 16 16"><path d="M3 13l1-4 7-7 3 3-7 7z" fill="none" stroke="currentColor" stroke-width="1.4"/><path d="M2 15h12" stroke="currentColor" stroke-width="1.4"/></symbol>
  <symbol id="i-remove" viewBox="0 0 16 16"><circle cx="8" cy="8" r="6.3" fill="none" stroke="currentColor" stroke-width="1.4"/><path d="M5.5 5.5l5 5M10.5 5.5l-5 5" stroke="currentColor" stroke-width="1.5"/></symbol>
</svg>

<div class="abs hero"></div>

<div class="abs user">
  <div class="gear"><svg width="13" height="13" viewBox="0 0 16 16"><circle cx="8" cy="8" r="5.5" fill="none" stroke="#e8b923" stroke-width="3" stroke-dasharray="2.2 1.4"/><circle cx="8" cy="8" r="3" fill="#e8b923"/><circle cx="8" cy="8" r="1.4" fill="#1b3f66"/></svg></div>
  <span class="user-name">Dana Holt</span>
</div>
<svg class="abs chev" width="10" height="7" viewBox="0 0 10 7"><path d="M1 1l4 4 4-4" fill="none" stroke="#fff" stroke-width="1.5"/></svg>

<div class="abs tool" style="left:359px"><svg width="12" height="12" viewBox="0 0 16 16"><rect x="2" y="3" width="11" height="11" fill="none" stroke="#fff" stroke-width="1.6"/><path d="M7 10l1-3 6-6 2 2-6 6z" fill="#fff"/></svg></div>
<div class="abs tool" style="left:409px"><svg width="12" height="12" viewBox="0 0 16 16"><rect x="1" y="4" width="10" height="10" fill="none" stroke="#fff" stroke-width="1.6"/><rect x="5" y="1" width="10" height="10" fill="#fff"/></svg></div>
<div class="abs tool" style="left:456px"><svg width="11" height="12" viewBox="0 0 14 16"><path d="M1 3h12M5 3V1h4v2" stroke="#fff" stroke-width="1.6" fill="none"/><path d="M2.5 4.5h9l-1 11h-7z" fill="#fff"/></svg></div>

<div class="abs meta" style="left:300px;width:152px">
  <div class="meta-field" style="left:61px"><div class="meta-label">Last Updated by</div><div class="meta-value">harbor.test</div></div>
</div>
<div class="abs meta" style="left:469px;width:324px">
  <div class="meta-field" style="left:18px"><div class="meta-label">Security Token</div><div class="meta-value">tadkaji4234ifndkn3</div></div>
  <div class="meta-field" style="left:153px"><div class="meta-label">Connected App</div><div class="meta-value">No</div></div>
  <div class="meta-field" style="left:240px"><div class="meta-label">Created By</div><div class="meta-value">harbor.test</div></div>
</div>
<div class="abs meta" style="left:810px;width:324px">
  <div class="meta-field" style="left:18px"><div class="meta-label">Data Source Name</div><div class="meta-value">Cloudledger - Sandbox</div></div>
  <div class="meta-field" style="left:152px"><div class="meta-label">Status</div><div class="meta-value">Active</div></div>
  <div class="meta-field" style="left:232px"><div class="meta-label">Last Updated by</div><div class="meta-value">harbor.test</div></div>
</div>

<div class="abs add-fields">Add Fields</div>

<section class="abs card open">
  <div class="abs toggle"><svg width="9" height="9" viewBox="0 0 10 10"><path d="M1 5h8" stroke="#3277b5" stroke-width="1.8"/></svg></div>
  <div class="abs rule" style="top:41px"></div>
  <div class="abs th" style="left:8px">Data Type</div>
  <svg class="abs" style="left:83px;top:60px" width="7" height="8" viewBox="0 0 7 8"><path d="M3.5 0v7M1 4.5l2.5 2.5L6 4.5" fill="none" stroke="#5f6673" stroke-width="1"/></svg>
  <div class="abs th" style="left:211px">Primary Key</div>
  <div class="abs th" style="left:353px">Rule Types</div>
  <div class="abs th" style="left:584px">Sensitive Data</div>
  <div class="abs th" style="left:730px">Actions</div>
  <div class="abs rule" style="top:74px"></div>

  <div class="abs row-text" style="left:7px;top:95px">Common.Text</div>
  <div class="abs row-text" style="left:7px;top:123px">Address. Address Line 3</div>
  <div class="abs row-text" style="left:7px;top:151px">Common ID</div>
  <div class="abs row-text" style="left:7px;top:179px">Address. Address Line 2</div>

  <div class="abs check on" style="left:235px;top:96px"><svg width="9" height="9" viewBox="0 0 10 10"><path d="M1.5 5l2.5 2.5L8.5 2" fill="none" stroke="#fff" stroke-width="1.4"/></svg></div>
  <div class="abs check" style="left:235px;top:124px"></div>
  <div class="abs check" style="left:235px;top:152px"></div>
  <div class="abs check" style="left:235px;top:180px"></div>

  <div class="abs" style="left:352px;top:94px">
    <svg width="450" height="100" viewBox="0 0 450 100" style="color:#9aa1ad;fill:#9aa1ad">
      <g id="rowicons">
        <text x="0" y="11" font-family="Lato,sans-serif" font-size="15" fill="#9aa1ad">a</text>
        <use href="#i-search" x="22" y="1" width="11" height="11"/>
        <use href="#i-copy" x="47" y="1" width="11" height="11"/>
        <use href="#i-share" x="73" y="0" width="12" height="12" style="color:#1c2230;fill:#1c2230"/>
        <use href="#i-target" x="100" y="1" width="11" height="11"/>
        <use href="#i-play" x="125" y="1" width="10" height="11"/>
        <use href="#i-clip" x="225" y="1" width="11" height="11"/>
        <use href="#i-card" x="250" y="0" width="13" height="13"/>
        <use href="#i-person" x="281" y="0" width="11" height="12"/>
        <use href="#i-pencil" x="370" y="0" width="12" height="12" style="color:#3277b5"/>
        <use href="#i-remove" x="399" y="0" width="12" height="12" style="color:#c99a0e"/>
      </g>
      <use href="#rowicons" y="28"/>
      <use href="#rowicons" y="56"/>
      <use href="#rowicons" y="84"/>
    </svg>
  </div>
</section>

<section class="abs card" style="top:484px;height:45px"><div class="abs toggle"><svg width="9" height="9" viewBox="0 0 10 10"><path d="M1 5h8M5 1v8" stroke="#3277b5" stroke-width="1.8"/></svg></div></section>
<section class="abs card" style="top:540px;height:45px"><div class="abs toggle"><svg width="9" height="9" viewBox="0 0 10 10"><path d="M1 5h8M5 1v8" stroke="#3277b5" stroke-width="1.8"/></svg></div></section>
<section class="abs card" style="top:596px;height:46px"><div class="abs toggle"><svg width="9" height="9" viewBox="0 0 10 10"><path d="M1 5h8M5 1v8" stroke="#3277b5" stroke-width="1.8"/></svg></div></section>

<nav class="abs rail">
  <div class="abs brand"><span class="brand-dot"></span>Vela</div>
  <div class="abs rail-item" style="top:91px"><svg viewBox="0 0 20 20"><circle cx="6" cy="6" r="2.6"/><circle cx="14" cy="6" r="2.6"/><circle cx="10" cy="7" r="3"/><path d="M1 15c0-3 2-5 5-5h8c3 0 5 2 5 5z"/></svg></div>
  <div class="abs rail-item" style="top:158px"><svg viewBox="0 0 20 20"><path d="M5 16a4 4 0 010-8 5 5 0 019.5-1A4.5 4.5 0 0115 16z"/></svg></div>
  <div class="abs rail-item active" style="top:227px"><svg viewBox="0 0 20 20"><path d="M5 2h7l4 4v12H5z"/></svg></div>
  <div class="abs rail-item" style="top:291px"><svg viewBox="0 0 20 20"><path d="M5 4h10v14H5z"/><rect x="8" y="2" width="4" height="3"/><path d="M7.5 11l2 2 3.5-4" stroke="#111823" stroke-width="1.6" fill="none"/></svg></div>
  <div class="abs rail-item" style="top:358px"><svg viewBox="0 0 20 20"><path d="M3 4h14v14H3z"/><path d="M5 9h2v2H5zM9 9h2v2H9zM13 9h2v2h-2zM5 13h2v2H5zM9 13h2v2H9zM13 13h2v2h-2z" fill="#111823"/><rect x="3" y="2" width="2" height="3"/><rect x="15" y="2" width="2" height="3"/></svg></div>
  <div class="abs rail-item" style="top:418px"><svg viewBox="0 0 20 20"><circle cx="10" cy="10" r="7"/><path d="M12.5 8a3 3 0 100 4" stroke="#111823" stroke-width="1.6" fill="none"/></svg></div>
</nav>

<aside class="abs sources">
  <h1 class="abs sources-title">Data Sources</h1>
  <div class="abs add-source"><svg width="10" height="10" viewBox="0 0 10 10"><path d="M1 5h8M5 1v8" stroke="#c99a0e" stroke-width="2"/></svg></div>
  <div class="abs search"><svg width="12" height="12" viewBox="0 0 16 16"><circle cx="9.5" cy="6.5" r="4.5" fill="none" stroke="#555" stroke-width="1.5"/><path d="M6 10l-4 4" stroke="#555" stroke-width="1.8"/></svg>Search</div>

  <div class="abs source selected" style="top:121px"><div class="source-name">Cloudledger - Sandbox</div><div class="source-type">Cloudledger.io</div></div>
  <div class="abs source" style="top:185px"><div class="source-name">Strata Test 1 (administrator)</div><div class="source-type">StrataSQL</div></div>
  <div class="abs source" style="top:249px"><div class="source-name">Strata Test 2 (administrator)</div><div class="source-type">StrataSQL</div></div>
  <div class="abs source" style="top:312px"><div class="source-name">Sadga</div><div class="source-type">Cloudledger.io</div></div>
  <div class="abs source" style="top:375px"><div class="source-name">Cloudledger Test 1 (masterd ev)</div><div class="source-type">StrataSQL</div></div>
  <div class="abs source" style="top:438px"><div class="source-name">CLDR - Field Entry</div><div class="source-type">Cloudledger.io</div></div>
  <div class="abs source" style="top:502px"><div class="source-name">CLDR 44</div><div class="source-type">Cloudledger.io</div></div>
  <div class="abs source" style="top:565px"><div class="source-name">CLDR 66</div><div class="source-type">Cloudledger.io</div></div>
</aside>
</body>
</html>
```